Business Card Re-Design/Update

We'd like to update out business cards. I've included our current "Style guide" which has the colour scheme of the organisation in it. I've also included the branding files with logos etc in them.

I've also included a copy of one of our existing cards so that you can see how ugly/dated they look. I'd like a fresh modern corporate look.

Target Market(s)

These are for our clients, potential clients, industry contacts - like all business cards

Contact Information for Business Card

Name
Position
Company Address - Level 1, 47 Fernby Street, Carlow Qld 4072
Direct Phone
mobile
Email
Website -www.korvalit.com.au
Logo

Colors

Designer to choose colors to be used in the design.

Requirements
Must have
• Main Logo
• Cards will need to be editable to be able to personalize them for each new employee.
Nice to have
• The MapOut, ShipWell, KeepSteady would be okay to have if they can be sensibly and professionally added to the look without detracting from the main imagery.
• Maybe they could go on the back of the card? will leave this to your creative discretion as to whether/where they fit.
Should not have
• Should not have decorative or script fonts

```html
<!DOCTYPE html>
<html lang="en">
<head>
<meta charset="utf-8">
<title>korvalIT Business Card</title>
<link href="https://fonts.googleapis.com/css2?family=Questrial&family=Arimo:wght@400;700&display=swap" rel="stylesheet">
<style>
  :root {
    --backdrop: #8c8c8c;
    --card-white: #f3f3f3;
    --brand-red: #d71920;
    --ink-dark: #3a3a3a;
    --ink-body: #444444;
    --logo-tint: #f2a9ad;
  }
  * { margin: 0; padding: 0; box-sizing: border-box; }
  html, body {
    width: 1200px;
    height: 900px;
    overflow: hidden;
    background: var(--backdrop);
  }
  .card {
    position: absolute;
    top: 200px;
    width: 310px;
    height: 502px;
    box-shadow: 2px 3px 4px rgba(0,0,0,0.45);
  }
  .card--front {
    left: 308px;
    background: var(--card-white);
    border-radius: 60px 0 60px 0;
  }
  .card--back {
    left: 641px;
    background: var(--brand-red);
    border-radius: 0 60px 0 60px;
  }
  .brand {
    position: absolute;
    left: 0;
    width: 100%;
    text-align: center;
  }
  .brand__mark {
    display: block;
    width: 34px;
    height: 34px;
    margin: 0 auto 18px;
  }
  .brand__name {
    font-family: "Questrial", sans-serif;
    font-size: 40px;
    line-height: 1;
    letter-spacing: 0.3px;
  }
  .card--front .brand { top: 62px; padding-left: 72px; }
  .card--front .brand__mark { background: var(--brand-red); }
  .card--front .brand__name { color: var(--ink-dark); }
  .card--back .brand { top: 370px; }
  .card--back .brand__mark { background: var(--logo-tint); }
  .card--back .brand__name { color: var(--logo-tint); }

  .contact {
    position: absolute;
    left: 27px;
    top: 272px;
    font-family: "Arimo", sans-serif;
    color: var(--ink-body);
    font-size: 14px;
    line-height: 20px;
  }
  .contact__name {
    color: var(--brand-red);
    font-weight: 700;
    font-size: 18px;
    line-height: 22px;
  }
  .contact__role { margin-bottom: 18px; }
  .contact__label { color: var(--brand-red); }
  .contact__address { margin-top: 16px; }
</style>
</head>
<body>
  <section class="card card--front">
    <div class="brand">
      <span class="brand__mark"></span>
      <div class="brand__name">korvalIT</div>
    </div>
    <div class="contact">
      <div class="contact__name">Daniel Hargrove</div>
      <div class="contact__role">Position</div>
      <div><span class="contact__label">M:</span> 412 309 55817</div>
      <div><span class="contact__label">P:</span> 412 309 55817</div>
      <div><span class="contact__label">E:</span> info@korvalit.com.au</div>
      <div><span class="contact__label">W:</span> www.korvalit.com.au</div>
      <div class="contact__address">Level 1, 47 Fernby Street,<br>Carlow Qld 4072</div>
    </div>
  </section>

  <section class="card card--back">
    <div class="brand">
      <span class="brand__mark"></span>
      <div class="brand__name">korvalIT</div>
    </div>
  </section>
</body>
</html>
```